Sparrow Haulage needs a business card design.

Design a double-sided business card for new freight business. On the front, would like to see our logo along with the following info:

Martin Obuya
CEO/FOUNDER
555-206-7142
martinobuya@sparrow-haulage.example

On the reverse side, we would like to use the graphic image of our logo only without the Sparrow Haulage name.

```html
<!DOCTYPE html>
<html lang="en">
<head>
<meta charset="utf-8">
<title>Sparrow Haulage – Business Card</title>
<link href="https://fonts.googleapis.com/css2?family=Arimo:wght@400;700&display=swap" rel="stylesheet">
<style>
  :root {
    --backdrop: #2b2b2b;
    --card: #0b0b0b;
    --navy: #141a80;
    --red: #c41212;
    --ink: #e6e6e6;
    --rule: #333333;
  }
  html, body {
    margin: 0;
    width: 1200px;
    height: 900px;
    overflow: hidden;
    background: var(--backdrop);
    font-family: "Arimo", Arial, sans-serif;
  }
  .canvas {
    width: 1200px;
    height: 900px;
    display: flex;
    flex-direction: column;
    align-items: center;
    justify-content: center;
    gap: 50px;
  }
  .card {
    width: 700px;
    height: 400px;
    background: var(--card);
    position: relative;
    box-shadow: 0 10px 30px rgba(0,0,0,.5);
  }
  .card--front {
    display: flex;
    align-items: center;
  }
  .brand {
    display: flex;
    align-items: center;
    gap: 12px;
  }
  .brand__square {
    width: 22px;
    height: 22px;
    background: var(--red);
    flex: none;
  }
  .brand__name {
    font-weight: 700;
    color: var(--red);
    letter-spacing: 3px;
    text-transform: uppercase;
    line-height: 1.05;
  }
  .card--front .brand {
    width: 330px;
    justify-content: center;
    margin-top: 60px;
  }
  .card--front .brand__name { font-size: 22px; }
  .divider {
    width: 1px;
    height: 200px;
    background: var(--rule);
  }
  .contact {
    padding-left: 34px;
    color: var(--ink);
  }
  .contact__name {
    font-size: 28px;
    font-weight: 700;
    margin: 0;
    text-transform: uppercase;
  }
  .contact__name .first { color: var(--navy); }
  .contact__name .last { color: var(--red); }
  .contact__role {
    font-size: 18px;
    margin: 4px 0 30px;
  }
  .contact__list {
    list-style: none;
    margin: 0;
    padding: 0;
    font-size: 15px;
  }
  .contact__list li {
    display: flex;
    align-items: center;
    gap: 10px;
    margin-bottom: 6px;
  }
  .contact__list li:first-child { font-size: 19px; }
  .icon { width: 16px; height: 16px; flex: none; }
  .card--back {
    display: flex;
    align-items: center;
    justify-content: center;
  }
  .back-mark {
    width: 70px;
    height: 70px;
    background: var(--red);
  }
</style>
</head>
<body>
<main class="canvas">
  <section class="card card--front">
    <div class="brand">
      <span class="brand__square"></span>
      <span class="brand__name">Sparrow<br>Haulage</span>
    </div>
    <div class="divider"></div>
    <div class="contact">
      <h1 class="contact__name"><span class="first">Martin</span> <span class="last">Obuya</span></h1>
      <p class="contact__role">CEO/FOUNDER</p>
      <ul class="contact__list">
        <li>
          <svg class="icon" viewBox="0 0 16 16"><path fill="#c41212" d="M3 1l3 3-1.5 2a9 9 0 0 0 5.5 5.5L12 10l3 3-2 2C6 15 1 10 1 3z"/></svg>
          555-206-7142
        </li>
        <li>
          <svg class="icon" viewBox="0 0 16 16"><rect x="1" y="3" width="14" height="10" fill="#c41212"/><path d="M1 3l7 6 7-6" fill="none" stroke="#0b0b0b" stroke-width="1.4"/></svg>
          martinobuya@sparrow-haulage.example
        </li>
        <li>
          <svg class="icon" viewBox="0 0 16 16"><circle cx="8" cy="8" r="7" fill="#c41212"/><g fill="none" stroke="#0b0b0b" stroke-width="1"><ellipse cx="8" cy="8" rx="3" ry="7"/><path d="M1 8h14M2.5 4.5h11M2.5 11.5h11"/></g></svg>
          www.sparrow-haulage.example
        </li>
      </ul>
    </div>
  </section>
  <section class="card card--back">
    <div class="back-mark" role="img" aria-label="Company logo symbol"></div>
  </section>
</main>
</body>
</html>
```